Wealth Education Business Needs Sharp Business Card Design

We need a business card design for a recently launched investor education business called Harbor Crest.

The final design should promote security, empowerment, self improvement and financial gain. The card will ideally promote the stature of the business.

For more information and colours please visit harborcrest.com.au

Target Market(s)

Corporate executives and high net worth individuals

Industry/Entity Type

Education

Contact Information for Business Card

```html
<!DOCTYPE html>
<html lang="en">
<head>
<meta charset="utf-8">
<title>Harbor Crest – Business Card</title>
<link rel="stylesheet" href="https://fonts.googleapis.com/css2?family=Questrial&display=swap">
<style>
  :root {
    --page-bg: #e9ebec;
    --card-bg: #f8f9f9;
    --card-edge: #c9cdcf;
    --ink: #1f2326;
    --teal: #137a7c;
    --mark-fill: #1a8a8f;
    --icon: #1e6f7a;
  }
  * { box-sizing: border-box; margin: 0; padding: 0; }
  html, body {
    width: 1200px;
    height: 970px;
    overflow: hidden;
    background: var(--page-bg);
    font-family: "Questrial", "Century Gothic", sans-serif;
    color: var(--ink);
  }
  .business-card {
    position: absolute;
    left: 100px;
    top: 205px;
    width: 1000px;
    height: 560px;
    background: var(--card-bg);
    border: 1px solid var(--card-edge);
    box-shadow: 0 10px 30px rgba(0,0,0,0.08);
  }
  .brand {
    position: absolute;
    left: 60px;
    top: 62px;
    display: flex;
    align-items: center;
    gap: 16px;
  }
  .brand-dot {
    width: 44px;
    height: 44px;
    border-radius: 50%;
    background: var(--mark-fill);
  }
  .brand-name {
    font-size: 40px;
    letter-spacing: 3px;
    text-transform: uppercase;
    color: var(--ink);
  }
  .holder {
    position: absolute;
    left: 60px;
    top: 245px;
  }
  .holder-name {
    font-size: 25px;
    font-weight: 700;
    color: var(--teal);
    letter-spacing: 0.3px;
  }
  .holder-role {
    font-size: 22px;
    margin-top: 2px;
  }
  .address {
    position: absolute;
    left: 60px;
    top: 322px;
    font-size: 22px;
    line-height: 29px;
    font-style: normal;
  }
  .contact-list {
    position: absolute;
    left: 60px;
    top: 390px;
    list-style: none;
    font-size: 22px;
    line-height: 27px;
  }
  .contact-list li {
    display: flex;
    align-items: center;
    gap: 8px;
  }
  .contact-list svg {
    width: 16px;
    height: 16px;
    fill: var(--icon);
    flex: none;
  }
  .feature-shape {
    position: absolute;
    left: 625px;
    top: 140px;
    width: 300px;
    height: 300px;
    border-radius: 50%;
    background: var(--mark-fill);
    opacity: 0.85;
  }
</style>
</head>
<body>
  <main class="business-card">
    <div class="brand">
      <span class="brand-dot"></span>
      <span class="brand-name">Harbor Crest</span>
    </div>

    <div class="holder">
      <p class="holder-name">Daniel Ashford</p>
      <p class="holder-role">Founder / CEO</p>
    </div>

    <address class="address">
      27 Coral Bay Road<br>
      Ashvale VIC 3891
    </address>

    <ul class="contact-list">
      <li>
        <svg viewBox="0 0 16 16" aria-hidden="true"><path d="M4 1h8a1 1 0 0 1 1 1v12a1 1 0 0 1-1 1H4a1 1 0 0 1-1-1V2a1 1 0 0 1 1-1zm1 2v9h6V3H5zm3 10a.8.8 0 1 0 0 1.6.8.8 0 0 0 0-1.6z"/></svg>
        999 999 9999
      </li>
      <li>
        <svg viewBox="0 0 16 16" aria-hidden="true"><path d="M1 5c0-2 3-3 7-3s7 1 7 3v1h-3.5V4.8C10.5 4.3 9.3 4 8 4s-2.5.3-3.5.8V6H1V5zm3 2h8l2 4v3H2v-3l2-4zm4 1.5a2 2 0 1 0 0 4 2 2 0 0 0 0-4z"/></svg>
        999 999 9999
      </li>
      <li>
        <svg viewBox="0 0 16 16" aria-hidden="true"><path d="M1 3h14v10H1V3zm1.5 1.2L8 8.5l5.5-4.3H2.5zM2 5.3V12h12V5.3L8 10 2 5.3z"/></svg>
        info@harborcrest.com.au
      </li>
      <li>
        <svg viewBox="0 0 16 16" aria-hidden="true"><path d="M8 1a7 7 0 1 0 0 14A7 7 0 0 0 8 1zm5.4 6.2h-2.5a11 11 0 0 0-.8-4 5.6 5.6 0 0 1 3.3 4zM8 2.5c.6.8 1.3 2.4 1.4 4.7H6.6C6.7 4.9 7.4 3.3 8 2.5zM5.9 3.2a11 11 0 0 0-.8 4H2.6a5.6 5.6 0 0 1 3.3-4zM2.6 8.8h2.5a11 11 0 0 0 .8 4 5.6 5.6 0 0 1-3.3-4zM8 13.5c-.6-.8-1.3-2.4-1.4-4.7h2.8c-.1 2.3-.8 3.9-1.4 4.7zm2.1-.7a11 11 0 0 0 .8-4h2.5a5.6 5.6 0 0 1-3.3 4z"/></svg>
        www.harborcrest.com.au
      </li>
    </ul>

    <div class="feature-shape" role="img" aria-label="Large brand symbol area in blue, teal and green tones"></div>
  </main>
</body>
</html>
```